Business Card Design Project

Business and Appointment Card for Medical Practice. On back of card we would like to have: blank line for patient name, Mon-Fri each with a check box next to the day, blank line for appointment date, blank line for appointment time, with option to circle am or pm.

Target Market(s)

Professional Business Associates, as well as function as patient appointment cards (on back side of card)

Industry/Entity Type

Business

Colors

Designer to choose colors to be used in the design.

```html
<!DOCTYPE html>
<html lang="en">
<head>
<meta charset="utf-8">
<title>Birch Hollow Medical Associates – Appointment Card</title>
<link href="https://fonts.googleapis.com/css2?family=Cinzel:wght@600&family=Montserrat:wght@400&display=swap" rel="stylesheet">
<style>
  :root {
    --backdrop: #d9d9d9;
    --card: #ffffff;
    --forest: #0f5b32;
    --cherry: #8c1b1e;
    --field: #ffffff;
    --label: #ffffff;
  }
  * { box-sizing: border-box; margin: 0; padding: 0; }
  html, body { width: 983px; height: 1200px; overflow: hidden; }
  body { background: var(--backdrop); position: relative; font-family: "Montserrat", Arial, sans-serif; }

  .card {
    position: absolute;
    left: 128px;
    width: 726px;
    height: 425px;
    background: var(--card);
    overflow: hidden;
  }
  .card--front { top: 114px; }
  .card--back { top: 654px; }

  .brand-mark { position: absolute; display: block; }

  .wordmark {
    position: absolute;
    width: 480px;
    text-align: center;
    font-family: "Cinzel", Georgia, serif;
    font-weight: 600;
    white-space: nowrap;
  }
  .wordmark .brand-name {
    display: block;
    font-size: 60px;
    line-height: 64px;
    color: var(--cherry);
  }
  .wordmark .descriptor {
    display: block;
    font-size: 34px;
    line-height: 36px;
    letter-spacing: 1px;
    color: var(--forest);
  }

  /* appointment side */
  .card--front .brand-mark { left: 58px; top: 22px; width: 104px; height: 104px; }
  .card--front .wordmark { left: 199px; top: 22px; }

  .band { position: absolute; left: 0; width: 100%; }
  .band--patient { top: 152px; height: 84px; background: var(--forest); }
  .band--appointment { top: 236px; height: 154px; background: var(--cherry); }

  .field-label {
    position: absolute;
    color: var(--label);
    font-size: 20px;
    line-height: 24px;
    white-space: nowrap;
  }
  .field-line { position: absolute; background: var(--field); }
  .tick-box { position: absolute; width: 18px; height: 18px; background: var(--field); }

  /* brand side */
  .card--back .brand-mark { left: 273px; top: 54px; width: 180px; height: 180px; }
  .card--back .wordmark { left: 123px; top: 246px; }
</style>
</head>
<body>

<section class="card card--front" aria-label="Appointment side">
  <svg class="brand-mark" viewBox="0 0 100 100" aria-hidden="true"><circle cx="50" cy="50" r="49" fill="var(--forest)"/></svg>
  <p class="wordmark"><span class="brand-name">Birch Hollow</span><span class="descriptor">Medical Associates</span></p>

  <div class="band band--patient">
    <span class="field-label" style="left:43px; top:32px;">Patient Name :</span>
    <span class="field-line" style="left:212px; top:28px; width:463px; height:33px;"></span>
  </div>

  <div class="band band--appointment">
    <span class="field-label" style="left:42px; top:31px;">Appointment Date :</span>
    <span class="field-line" style="left:263px; top:30px; width:199px; height:26px;"></span>

    <span class="field-label" style="left:195px; top:99px;">Time :</span>
    <span class="field-line" style="left:263px; top:98px; width:90px; height:26px;"></span>
    <span class="field-label" style="left:368px; top:99px;">a.m.</span>
    <span class="tick-box" style="left:424px; top:103px;"></span>
    <span class="field-label" style="left:452px; top:99px;">p.m.</span>
    <span class="tick-box" style="left:507px; top:103px;"></span>
  </div>
</section>

<section class="card card--back" aria-label="Brand side">
  <svg class="brand-mark" viewBox="0 0 100 100" aria-hidden="true"><circle cx="50" cy="50" r="49" fill="var(--forest)"/></svg>
  <p class="wordmark"><span class="brand-name">Birch Hollow</span><span class="descriptor">Medical Associates</span></p>
</section>

</body>
</html>
```